We need a logo design that explain all the products we possess.
The main goal is to represent graphically all the logos, pointing to one single logo - Vellamor.
The descriptions are in french.
I have uploaded a file with 4 logos to use:
Vellamor (the logo that all the rest should be pointing to)
RTN
Ombrevik
TroupéLune
All logo must be used in the vector graphic format, the description file is in each folder, it's the description that should be next to the logo.

The main goal of this is to create a banner 10' x 11' (estimated)

Target Market(s)

Cities

Requirements
Must have
• All the logos in the zip file in vector graphic.
Nice to have
• A background
Should not have
• Do not use KOL logo, it's a mix with RTN, and Kol Blue/dark blue with inscription "RTN", Charging fees for a part of the picture is not ok!

```html
<!DOCTYPE html>
<html lang="fr">
<head>
<meta charset="utf-8">
<title>Vellamor – gamme de produits</title>
<link rel="stylesheet" href="https://fonts.googleapis.com/css2?family=Montserrat:wght@500;700;800&display=swap">
<style>
  :root {
    --page: #ffffff;
    --red: #cc2229;
    --yellow: #fff12a;
    --grey: #a7a8aa;
    --blue: #4773b3;
    --ink-blue: #2f5aa8;
    --sky: #58a8e0;
    --white: #ffffff;
  }
  html, body {
    margin: 0;
    width: 1164px;
    height: 1200px;
    overflow: hidden;
    background: var(--page);
  }
  .banner {
    display: block;
    width: 1164px;
    height: 1200px;
  }
  .panel-red { fill: var(--red); }
  .panel-yellow { fill: var(--yellow); stroke: var(--white); stroke-width: 4; }
  .panel-grey { fill: var(--grey); stroke: var(--white); stroke-width: 4; }
  .panel-blue { fill: var(--blue); stroke: var(--white); stroke-width: 4; }
  .brand-name {
    font-family: "Montserrat", sans-serif;
    text-anchor: middle;
  }
  .brand-vellamor { fill: var(--ink-blue); font-weight: 800; font-size: 34px; letter-spacing: 1px; }
  .brand-ombrevik { fill: var(--ink-blue); font-weight: 500; font-size: 24px; letter-spacing: 5px; }
  .brand-rtn { fill: var(--white); font-weight: 700; font-size: 32px; letter-spacing: 1px; }
  .brand-troupelune { fill: var(--sky); font-weight: 700; font-size: 34px; }
  .brand-dot-vellamor { fill: var(--ink-blue); }
  .brand-dot-ombrevik { fill: var(--ink-blue); }
  .brand-dot-rtn { fill: var(--white); }
  .brand-dot-troupelune { fill: var(--sky); }
</style>
</head>
<body>
<svg class="banner" viewBox="0 0 989 1020" preserveAspectRatio="none" xmlns="http://www.w3.org/2000/svg">
  <rect class="panel-red" x="194" y="178" width="612" height="674"/>

  <g class="section section-vellamor">
    <polygon class="panel-yellow" points="246,176 500,176 500,488 376,566 246,494"/>
    <circle class="brand-dot-vellamor" cx="373" cy="400" r="26"/>
    <text class="brand-name brand-vellamor" x="373" y="472">VELLAMOR</text>
  </g>

  <g class="section section-ombrevik">
    <polygon class="panel-grey" points="502,176 808,176 808,316 502,488"/>
    <circle class="brand-dot-ombrevik" cx="645" cy="265" r="26"/>
    <text class="brand-name brand-ombrevik" x="645" y="334">OMBREVIK</text>
  </g>

  <g class="section section-rtn">
    <polygon class="panel-blue" points="378,568 808,318 808,816"/>
    <circle class="brand-dot-rtn" cx="658" cy="548" r="30"/>
    <text class="brand-name brand-rtn" x="658" y="648">RTN</text>
  </g>

  <g class="section section-troupelune">
    <circle class="brand-dot-troupelune" cx="378" cy="690" r="30"/>
    <text class="brand-name brand-troupelune" x="378" y="782">TroupéLune</text>
  </g>
</svg>
</body>
</html>
```